Business Card for Professional Photographer

I'm looking for an eye catching modern clean design that compliments my logo/ website fonts & colours.
I specialise in architecture, corporate & commercial photography so I'm marketing to professional clients rather than portrait / wedding clients.

I would prefer to not have a solid black design.

My logo brand guide is as follows :

Main front font. : Reislust
Main font colour : #fff
Slogan front font : Ubuntu Bold
Monogram front font : Venti Medium
Container colour : #fff

I need print ready files in pdf .png & .eps formats.

Included in the files below are some screen grabs as reference to font & colours etc.

```html
<!DOCTYPE html>
<html lang="en">
<head>
<meta charset="utf-8">
<title>Clearline Studio — Business Card</title>
<link href="https://fonts.googleapis.com/css2?family=Montserrat:wght@300;400;600;700&family=Ubuntu:wght@500;700&family=Open+Sans:wght@400;600&display=swap" rel="stylesheet">
<style>
  :root{
    --stage:#202327;
    --gold-light:#f3e29a;
    --gold-mid:#d9b25e;
    --gold-deep:#c18a3c;
    --gold-text:#c99638;
    --gold-line:#d8b04a;
    --beige-ring:#e6ddce;
    --card-white:#ffffff;
    --ink-grey:#6d6d6d;
  }
  *{margin:0;padding:0;box-sizing:border-box;}
  html,body{width:1200px;height:900px;overflow:hidden;background:var(--stage);}
  .stage{position:relative;width:1200px;height:900px;}

  .card{position:absolute;overflow:hidden;border-radius:4px;box-shadow:0 10px 30px rgba(0,0,0,.45);}
  .card__rings{position:absolute;inset:0;width:100%;height:100%;}

  /* Back of card — gold */
  .card--back{left:470px;top:290px;width:560px;height:320px;
    background:radial-gradient(circle at 50% 48%,var(--gold-light) 0%,var(--gold-mid) 45%,var(--gold-deep) 100%);}
  .brand-lockup{position:absolute;left:0;right:0;top:118px;text-align:center;color:#fff;}
  .brand-lockup__row{display:inline-flex;align-items:center;gap:12px;}
  .brand-lockup__dot{width:18px;height:18px;border:2px solid #fff;border-radius:50%;}
  .brand-lockup__name{font-family:'Montserrat',sans-serif;font-weight:400;font-size:30px;letter-spacing:5px;}
  .brand-lockup__slogan{margin-top:10px;font-family:'Ubuntu',sans-serif;font-weight:700;font-size:11px;letter-spacing:2.5px;}

  /* Front of card — white */
  .card--front{left:170px;top:170px;width:320px;height:560px;background:var(--card-white);}
  .front-content{position:absolute;left:0;right:0;top:150px;text-align:center;}
  .front-brand{display:inline-flex;align-items:center;gap:8px;font-family:'Montserrat',sans-serif;font-weight:600;font-size:17px;letter-spacing:3px;color:var(--gold-text);}
  .front-brand__dot{width:13px;height:13px;border:2px solid var(--gold-text);border-radius:50%;}
  .person-name{margin-top:34px;font-family:'Montserrat',sans-serif;font-weight:700;font-size:21px;letter-spacing:1px;color:var(--gold-text);}
  .person-role{margin-top:2px;font-family:'Open Sans',sans-serif;font-size:15px;color:var(--gold-mid);}
  .rule{width:170px;height:1.5px;margin:12px auto;background:linear-gradient(90deg,var(--gold-deep),var(--gold-light),var(--gold-deep));}
  .contact-icons{display:flex;justify-content:center;gap:10px;margin-bottom:6px;}
  .contact-icons svg{width:16px;height:16px;}
  .contact-line{font-family:'Open Sans',sans-serif;font-size:13.5px;line-height:21px;color:var(--ink-grey);}
  .address{font-family:'Open Sans',sans-serif;font-size:14px;color:var(--ink-grey);}
</style>
</head>
<body>
<main class="stage">

  <section class="card card--front" aria-label="Business card front">
    <svg class="card__rings" viewBox="0 0 320 560" aria-hidden="true">
      <circle cx="175" cy="270" r="235" fill="none" stroke="var(--beige-ring)" stroke-width="34" opacity=".85"/>
    </svg>
    <div class="front-content">
      <div class="front-brand"><span class="front-brand__dot"></span>CLEARLINE</div>
      <h1 class="person-name">OWEN HARTLEY</h1>
      <p class="person-role">Photographer</p>
      <div class="rule"></div>
      <div class="contact-icons">
        <svg viewBox="0 0 16 16"><circle cx="8" cy="8" r="7" fill="none" stroke="var(--gold-text)" stroke-width="1.3"/><path d="M5.5 4.5l1.5 1.5-1 1c.6 1.2 1.4 2 2.6 2.6l1-1 1.5 1.5-1 1c-2.5-.3-4.8-2.6-5.1-5.1z" fill="var(--gold-text)"/></svg>
        <svg viewBox="0 0 16 16"><rect x="2" y="4" width="12" height="8" fill="none" stroke="var(--gold-text)" stroke-width="1.3"/><path d="M2 4l6 5 6-5" fill="none" stroke="var(--gold-text)" stroke-width="1.3"/></svg>
        <svg viewBox="0 0 16 16"><circle cx="8" cy="8" r="6.5" fill="none" stroke="var(--gold-text)" stroke-width="1.3"/><ellipse cx="8" cy="8" rx="3" ry="6.5" fill="none" stroke="var(--gold-text)" stroke-width="1.1"/><path d="M1.5 8h13" stroke="var(--gold-text)" stroke-width="1.1"/></svg>
      </div>
      <p class="contact-line">0400 555 318</p>
      <p class="contact-line">hello@clearlinestudio.com.au</p>
      <p class="contact-line">www.clearlinestudio.com.au</p>
      <div class="rule"></div>
      <p class="address">Eastern Highlands, Australia</p>
    </div>
  </section>

  <section class="card card--back" aria-label="Business card back">
    <svg class="card__rings" viewBox="0 0 560 320" aria-hidden="true">
      <circle cx="280" cy="155" r="150" fill="none" stroke="#ffffff" stroke-opacity=".12" stroke-width="40"/>
      <circle cx="280" cy="155" r="245" fill="none" stroke="#ffffff" stroke-opacity=".08" stroke-width="50"/>
    </svg>
    <div class="brand-lockup">
      <div class="brand-lockup__row"><span class="brand-lockup__dot"></span><span class="brand-lockup__name">CLEARLINE STUDIO</span></div>
      <p class="brand-lockup__slogan">Architecture Corporate Commercial</p>
    </div>
  </section>

</main>
</body>
</html>
```